Postcard Design January 2015

I need a postcard designed to introduce my company to potential new customers in the UK. My company is TW Page Works based in Chester and we represent one of Poland's leading and long established book printers. We offer competitive pricing, consistently high levels of print and binding quality and industry leading levels of customer service. We have been meeting the print requirements of UK publishers for more than 10 years.
Updates

```html
<!DOCTYPE html>
<html lang="en">
<head>
<meta charset="utf-8">
<title>TW Page Works – Postcard</title>
<link rel="stylesheet" href="https://fonts.googleapis.com/css2?family=Oswald:wght@300;400;500&display=swap">
<style>
  :root {
    --backdrop: #c4c5c9;
    --card: #ffffff;
    --accent: #c8b400;
    --body-text: #7b7b82;
    --rule: #d6d6d6;
    --photo-dark: #3a3a3a;
    --photo-mid: #8a8a8a;
    --page-light: #ece7de;
    --page-mid: #ddd2c2;
  }
  * { box-sizing: border-box; margin: 0; padding: 0; }
  html, body {
    width: 1200px;
    height: 996px;
    overflow: hidden;
    background: var(--backdrop);
  }
  .postcard {
    position: absolute;
    left: 40px;
    top: 102px;
    width: 1120px;
    height: 792px;
    background: var(--card);
    overflow: hidden;
    font-family: "Oswald", "Arial Narrow", sans-serif;
  }
  .headline-photo {
    position: absolute;
    left: 89px;
    top: 76px;
    width: 384px;
    height: 104px;
    background: linear-gradient(180deg, var(--photo-mid) 0%, var(--photo-dark) 55%, #555 100%);
    border-radius: 2px;
  }
  .divider-vertical {
    position: absolute;
    left: 543px;
    top: 31px;
    width: 1px;
    height: 581px;
    background: var(--rule);
  }
  .rule-left {
    position: absolute;
    left: 58px;
    top: 249px;
    width: 485px;
    height: 1px;
    background: var(--rule);
  }
  .rule-right {
    position: absolute;
    left: 544px;
    top: 495px;
    width: 521px;
    height: 1px;
    background: var(--rule);
  }
  .benefits {
    position: absolute;
    left: 77px;
    top: 318px;
    list-style: none;
    color: var(--accent);
    font-weight: 400;
    font-size: 24px;
    line-height: 52px;
    text-transform: uppercase;
  }
  .benefits li::before { content: "» "; }
  .intro {
    position: absolute;
    left: 618px;
    top: 110px;
    width: 425px;
    color: var(--body-text);
    font-weight: 400;
    font-size: 19.5px;
    line-height: 30.5px;
  }
  .intro p + p { margin-top: 14px; }
  .web-address {
    position: absolute;
    left: 618px;
    top: 534px;
    color: var(--accent);
    font-weight: 500;
    font-size: 30px;
    letter-spacing: 0.2px;
  }
  .books-photo {
    position: absolute;
    left: 0;
    top: 626px;
    width: 1120px;
    height: 166px;
    background: linear-gradient(90deg, var(--page-light) 0%, var(--page-mid) 50%, var(--page-light) 100%);
  }
</style>
</head>
<body>
  <article class="postcard">
    <div class="headline-photo" role="img" aria-label="Photo of metal letterpress type blocks spelling WE PRINT"></div>
    <div class="divider-vertical"></div>
    <div class="rule-left"></div>

    <ul class="benefits">
      <li>Competitive pricing</li>
      <li>Consistently high levels of print</li>
      <li>High binding quality</li>
      <li>Leading levels of customer service</li>
    </ul>

    <div class="intro">
      <p>We offer a truly competitive service to book publishers looking for excellence in book printing and binding, combined with a first rate service.</p>
      <p>There is of course a wide range of book printers currently available but very few succeed in consistently living up to expectations. At TW Page Works we ensure that your book printing requirements are fulfilled to your complete satisfaction. Finding the best available combination of price, print quality and service can be a time consuming process so why not let us do the work for you.</p>
    </div>

    <div class="rule-right"></div>
    <div class="web-address">WWW.TWPAGEWORKS.CO.UK</div>

    <div class="books-photo" role="img" aria-label="Photo of a row of books seen from the page edges"></div>
  </article>
</body>
</html>
```